Maplecrest Disability - Social Security Disability Attorneys

Our company is expanding to attract clients nationwide for our social security disability practice. We have a logo, but I am looking for a creative and elegant letterhead that projects an image of being technologically advanced but still professional enough for the legal field. I am looking for the "wow factor" combined with this is still professional enough for a law practice.

Requesting letterhead and business card design
Updates

Had to update and change the logo. The previous logo had a typo. Please send updates with the new logo for consideration. The letterhead and business cards should be professional enough to be used for a law firm. Thanks.

Industry/Entity Type

Law Practice, Law Firm, Healthcare Industry, Government

Colors

Designer to choose colors to be used in the design.

Requirements
Nice to have
• **Please create a vertical design for the business card**

```html
<!DOCTYPE html>
<html lang="en">
<head>
<meta charset="utf-8">
<title>Maplecrest Disability Letterhead</title>
<link rel="stylesheet" href="https://fonts.googleapis.com/css2?family=Cinzel:wght@400;500&family=Open+Sans:wght@400;600&display=swap">
<style>
  :root {
    --backdrop: #d6dadb;
    --paper: #ffffff;
    --brand-blue: #4169e1;
    --brand-orange: #f7802b;
    --ink: #555a60;
    --tagline: #6f7fae;
  }
  * { margin: 0; padding: 0; box-sizing: border-box; }
  html, body {
    width: 1200px; height: 784px; overflow: hidden;
    background: var(--backdrop);
  }
  .canvas {
    position: relative; width: 1200px; height: 784px;
    display: flex; align-items: center; justify-content: center;
  }
  .letterhead {
    position: relative; width: 572px; height: 740px;
    background: var(--paper);
    box-shadow: 0 2px 10px rgba(0,0,0,0.12);
    overflow: hidden;
  }
  .header {
    position: absolute; top: 28px; left: 0; right: 0; height: 40px;
  }
  .header-bar-left {
    position: absolute; left: 0; top: 2px; width: 30px; height: 10px;
    background: var(--brand-blue);
  }
  .brand {
    position: absolute; left: 40px; top: -2px;
    display: flex; flex-direction: column;
  }
  .brand-row { display: flex; align-items: center; gap: 6px; }
  .brand-mark {
    width: 8px; height: 8px; border-radius: 50%;
    background: var(--brand-orange);
  }
  .brand-name {
    font-family: "Cinzel", serif; font-weight: 500;
    font-size: 17px; letter-spacing: 1.2px; color: var(--brand-blue);
    line-height: 1;
  }
  .brand-tagline {
    margin-top: 4px;
    font-family: "Cinzel", serif; font-weight: 400;
    font-size: 5.6px; letter-spacing: 1.3px; color: var(--tagline);
    text-transform: uppercase;
  }
  .header-bar-right {
    position: absolute; left: 258px; right: 0; top: 17px; height: 8px;
    background: var(--brand-orange);
  }
  .footer {
    position: absolute; left: 0; bottom: 0; width: 572px; height: 74px;
  }
  .footer svg { display: block; }
  .contact-text {
    font-family: "Open Sans", sans-serif; font-size: 8.6px; fill: var(--ink);
  }
  .website-text {
    font-family: "Open Sans", sans-serif; font-weight: 600;
    font-size: 10.5px; fill: #ffffff;
  }
</style>
</head>
<body>
<main class="canvas">
  <article class="letterhead">
    <header class="header">
      <div class="header-bar-left"></div>
      <div class="brand">
        <div class="brand-row">
          <span class="brand-name">Maplecrest Disability</span>
          <span class="brand-mark"></span>
        </div>
        <span class="brand-tagline">Social Security Disability Attorneys</span>
      </div>
      <div class="header-bar-right"></div>
    </header>

    <footer class="footer">
      <svg width="572" height="74" viewBox="0 0 572 74" aria-label="Contact details">
        <g fill="var(--brand-orange)">
          <path d="M12 8.5a3 3 0 0 1 6 0c0 2.2-3 5.2-3 5.2s-3-3-3-5.2z"/>
          <circle cx="15" cy="8.5" r="1" fill="#fff"/>
        </g>
        <text class="contact-text" x="21" y="14">0000 Larkspur Ave, Ste 000, Dallas, TX 00001</text>

        <g fill="var(--brand-orange)">
          <rect x="220" y="6.5" width="8" height="8" rx="1.5"/>
          <path d="M222 9c0.5 2 1.5 3 3.5 3.5l0.8-0.9-1-0.6-0.5 0.5c-0.8-0.4-1.4-1-1.8-1.8l0.5-0.5-0.6-1z" fill="#fff"/>
        </g>
        <text class="contact-text" x="231" y="14">000-000-0000</text>

        <g fill="var(--brand-orange)">
          <rect x="299" y="8" width="8" height="6" rx="1"/>
          <rect x="301" y="5.5" width="4" height="3"/>
        </g>
        <text class="contact-text" x="310" y="14">000-000-0000</text>

        <g>
          <rect x="378" y="7" width="9" height="7" rx="1" fill="var(--brand-orange)"/>
          <path d="M378.5 7.8l4 3 4-3" stroke="#fff" stroke-width="0.9" fill="none"/>
        </g>
        <text class="contact-text" x="390" y="14">info@maplecrestdisability.com</text>

        <rect x="14" y="22" width="196" height="4" fill="var(--brand-orange)"/>
        <polygon points="214,22 290,22 294,26 214,26" fill="var(--brand-blue)"/>
        <polygon points="298,22 520,22 520,26 302,26" fill="var(--brand-orange)"/>

        <rect x="0" y="34" width="380" height="9" fill="var(--brand-blue)"/>
        <polygon points="376,30 572,30 572,74 392,74 392,43 380,43" fill="var(--brand-blue)"/>
        <text class="website-text" x="482" y="56" text-anchor="middle">www.maplecrestdisability.com</text>
      </svg>
    </footer>
  </article>
</main>
</body>
</html>
```